Sickle Cell Patient Flyer

I need this be appealing to families dealing with sickle cell disease. Both informative-introducing the idea that a stroke prevention program is not only easy for their children but necessary. Stroke is a risk to all with children with SCD.
I included a few info flyers from the Vessel Alliance and licensed to me photos I like. I am open to suggestions.
web address is brightpathwellbeing.net
Call to schedule 833-412-7086
TCD is a safe and accurate tool that makes stroke prevention possible for your SCD patients and family.
Risk is highest for SCD sufferers age 2 to 5. Protect your childs future.

Target Market(s)

Parents, families and medical professionals

Industry/Entity Type

Medical wellness

Font styles to use
Other font styles liked:
• something close to my logo font

Colors
0094D4
00A9DD
6FCCEA
C7EBF8
E9F6FB

Requirements
Nice to have
• pictures of kids (Children of color) pictures of Brains, kids happy with medical professionals
Should not have
• dark colors

```html
<!DOCTYPE html>
<html lang="en">
<head>
<meta charset="utf-8">
<title>Stroke Prevention for Children with Sickle Cell Disease</title>
<link href="https://fonts.googleapis.com/css2?family=Emilys+Candy&family=Arimo:wght@400;700&display=swap" rel="stylesheet">
<style>
  :root{
    --page:#ececec;
    --paper:#ffffff;
    --slate:#4b4b4b;
    --slate-dark:#2f2f2f;
    --navy:#16477d;
    --sky:#6ecbea;
    --sky-pale:#c7ebf8;
    --ink:#1c3f6e;
    --white:#ffffff;
  }
  *{box-sizing:border-box;margin:0;padding:0}
  html,body{width:1200px;height:1200px;overflow:hidden;background:var(--page)}
  body{position:relative;font-family:"Arimo",Arial,sans-serif}
  .flyer{position:absolute;left:170px;top:47px;width:860px;height:1106px;background:var(--paper);box-shadow:0 6px 22px rgba(0,0,0,.28);overflow:hidden}

  .hero{position:absolute;left:0;top:0;width:860px;height:465px;background:radial-gradient(ellipse at 65% 40%,#6a6a6a 0%,var(--slate) 45%,var(--slate-dark) 100%)}
  .hero-photo{position:absolute;left:330px;top:0;width:530px;height:465px;background:radial-gradient(ellipse at 58% 70%,rgba(240,180,30,.75) 0%,rgba(220,160,40,.45) 30%,rgba(90,90,90,0) 65%)}
  .hero-band{position:absolute;left:0;top:465px;width:860px;height:11px;background:var(--sky)}

  .brand{position:absolute;left:26px;top:70px;display:flex;align-items:center;gap:10px}
  .brand-mark{width:26px;height:26px;background:var(--sky)}
  .brand-name{font-family:"Emilys Candy",cursive;font-size:30px;color:var(--white);line-height:1}

  .headline{position:absolute;left:27px;top:222px;width:440px;font-family:"Emilys Candy",cursive;font-size:29px;line-height:37px;color:var(--white)}
  .intro{position:absolute;left:26px;top:386px;width:420px;font-size:17.5px;line-height:23px;color:var(--white)}

  .pill{position:absolute;height:31px;background:var(--navy);border-radius:9px;color:var(--white);font-family:"Emilys Candy",cursive;font-size:24px;line-height:31px;text-align:center}
  .pill-features{left:352px;top:488px;width:170px}
  .pill-facts{left:355px;top:622px;width:169px}

  .feature{position:absolute;top:531px;width:345px;height:70px;background:var(--sky);border-radius:9px;display:flex;align-items:center;padding-left:15px}
  .feature-a{left:65px}
  .feature-b{left:447px}
  .feature .badge{width:54px;height:54px;border-radius:50%;background:var(--navy);border:3px solid var(--white);flex:none;display:flex;align-items:center;justify-content:center}
  .feature .rule{width:3px;height:44px;background:var(--navy);margin:0 12px 0 13px;flex:none}
  .feature p{color:var(--white);font-size:16px;line-height:19px}

  .fact{position:absolute;display:flex;gap:0}
  .fact .icon{position:absolute;width:42px;height:42px;border-radius:50%;background:var(--sky-pale);border:2px solid var(--sky);display:flex;align-items:center;justify-content:center}
  .fact p{position:absolute;font-size:14.6px;line-height:18px;color:var(--ink);text-align:justify}
  .col-l .icon{left:42px}
  .col-l p{left:103px;width:307px}
  .col-r .icon{left:454px}
  .col-r p{left:511px;width:307px}

  .cta{position:absolute;left:87px;top:928px;width:686px;height:68px;border:2px solid var(--navy);border-radius:10px;padding:5px}
  .cta-inner{width:100%;height:100%;background:var(--sky);border-radius:7px;text-align:center;color:var(--white);padding-top:6px}
  .cta-inner strong{display:block;font-size:17px;line-height:21px}
  .cta-inner span{display:block;font-size:16.5px;line-height:24px}

  .tagline{position:absolute;left:0;top:1000px;width:860px;text-align:center;font-family:"Emilys Candy",cursive;font-size:34px;color:var(--navy);display:flex;justify-content:center;align-items:center;gap:22px}
  .tagline svg{flex:none}

  .footer{position:absolute;left:0;top:1048px;width:860px;height:58px}
  .footer svg{position:absolute;left:0;top:0}
  .footer .web{position:absolute;left:60px;top:22px;font-size:15.5px;color:var(--white)}
  .footer .web b{font-weight:700}
  .footer .call{position:absolute;left:466px;top:14px;font-size:15.5px;color:var(--white);display:flex;align-items:baseline;gap:5px}
  .footer .call b{font-size:26px;font-weight:700}
</style>
</head>
<body>
<main class="flyer">
  <section class="hero">
    <div class="hero-photo" role="img" aria-label="Photo of a smiling child in a yellow sweater raising both fists, with chalk brain drawings on a dark board behind"></div>
    <div class="brand"><span class="brand-mark"></span><span class="brand-name">BrightPath Wellbeing</span></div>
    <h1 class="headline">Stroke Prevention<br>for children with<br>children with<br>Sickle cell disease is possible!</h1>
    <p class="intro">TCD is a safe and accurate tool that makes stroke prevention possible for your SCD patients and family</p>
  </section>
  <div class="hero-band"></div>

  <h2 class="pill pill-features">Key Features</h2>
  <div class="feature feature-a">
    <span class="badge"><svg width="30" height="30" viewBox="0 0 30 30" fill="none" stroke="#fff" stroke-width="2"><circle cx="15" cy="15" r="12"/><line x1="6" y1="24" x2="24" y2="6"/><path d="M11 11a6 6 0 0 0 0 8M19 11a6 6 0 0 1 0 8"/></svg></span>
    <span class="rule"></span>
    <p>Simple and painless screening for your child</p>
  </div>
  <div class="feature feature-b">
    <span class="badge"><svg width="30" height="30" viewBox="0 0 30 30" fill="none" stroke="#fff" stroke-width="2"><path d="M10 8h8v8a4 4 0 0 1-8 0z"/><path d="M14 20v4h9"/><path d="M9 5a7 7 0 0 1 10 0"/></svg></span>
    <span class="rule"></span>
    <p>Our Screening uses ultrasound which is transcranial doppler</p>
  </div>

  <h2 class="pill pill-facts">Key Facts</h2>

  <div class="fact col-l">
    <span class="icon" style="top:667px"><svg width="24" height="24" viewBox="0 0 24 24" fill="none" stroke="#16477d" stroke-width="1.6"><circle cx="12" cy="12" r="9"/><circle cx="9" cy="10" r="2"/><circle cx="14" cy="14" r="2"/><circle cx="15" cy="8" r="1.5"/></svg></span>
    <p style="top:663px">Sickle cell disease (SCD) is a blood disorder in which misshapen or “sickled” red blood cells can clog blood vessels and cause complications such as stroke and blood vessel damage</p>
  </div>
  <div class="fact col-l">
    <span class="icon" style="top:771px"><svg width="24" height="24" viewBox="0 0 24 24" fill="none" stroke="#16477d" stroke-width="1.6"><path d="M8 3c0 6 8 12 8 18M16 3c0 6-8 12-8 18M9 8h6M9 16h6"/></svg></span>
    <p style="top:767px">The most severe form of the disease, called sickle cell anemia, occurs when a person inherits two abnormal copies of the hemoglobin-Beta gene</p>
  </div>
  <div class="fact col-l">
    <span class="icon" style="top:858px"><svg width="24" height="24" viewBox="0 0 24 24" fill="none" stroke="#16477d" stroke-width="1.6"><path d="M12 5c-4-2-8 1-7 5-2 2-1 6 2 6 1 3 5 3 5 0V5c4-2 8 1 7 5 2 2 1 6-2 6"/></svg></span>
    <p style="top:854px">Stroke risk increases over 100-fold in children with SCD compared to children without sickle cell disease</p>
  </div>

  <div class="fact col-r">
    <span class="icon" style="top:667px"><svg width="24" height="24" viewBox="0 0 24 24" fill="none" stroke="#16477d" stroke-width="1.6"><circle cx="12" cy="9" r="5"/><path d="M6 15c2 6 10 6 12 0"/></svg></span>
    <p style="top:663px">All babies in the U.S. are screened for sickle cell disease, which affects 1 in 2,400 children, and 1 in 400 Black children</p>
  </div>
  <div class="fact col-r">
    <span class="icon" style="top:736px"><span style="font-family:'Emilys Candy',cursive;font-size:16px;color:#16477d">11%</span></span>
    <p style="top:731px">About 11% of SCD patients have strokes before age 20 with the highest risk between age 2 and 5</p>
  </div>
  <div class="fact col-r">
    <span class="icon" style="top:803px"><svg width="24" height="24" viewBox="0 0 24 24" fill="none" stroke="#16477d" stroke-width="1.6"><path d="M4 12a8 7 0 1 1 3 5l-3 2 1-4"/><path d="M9 10v4M12 9v6M15 10v4"/></svg></span>
    <p style="top:798px">The common stroke in children with sickle cell disease is “silent strokes,” or “silent” injury to the brain.</p>
  </div>
  <div class="fact col-r">
    <span class="icon" style="top:870px"><svg width="24" height="24" viewBox="0 0 24 24" fill="none" stroke="#16477d" stroke-width="1.6"><path d="M8 20v-4c-3-2-3-8 1-10 4-2 9 0 9 5l2 3h-2v3h-3v3"/><path d="M12 7l-1 3h2l-1 3"/></svg></span>
    <p style="top:865px">There are two main types of strokes: Ischemicand hemorrhagic. Ischemic strokes are more common in children</p>
  </div>

  <div class="cta"><div class="cta-inner"><strong>Screening or early signs of stroke</strong><span>can be a tool to for early diagnosis allowing for treatments that eliminate the risk</span></div></div>

  <p class="tagline">
    <svg width="20" height="20" viewBox="0 0 20 20"><polygon fill="#6ecbea" points="10,1 12.6,7.2 19,7.6 14,11.8 15.6,18.4 10,14.8 4.4,18.4 6,11.8 1,7.6 7.4,7.2"/></svg>
    <span>Protect your childs future</span>
    <svg width="20" height="20" viewBox="0 0 20 20"><polygon fill="#6ecbea" points="10,1 12.6,7.2 19,7.6 14,11.8 15.6,18.4 10,14.8 4.4,18.4 6,11.8 1,7.6 7.4,7.2"/></svg>
  </p>

  <footer class="footer">
    <svg width="860" height="58" viewBox="0 0 860 58"><rect x="0" y="10" width="860" height="48" fill="#6ecbea"/><path d="M348 58 L395 0 H860 V58 Z" fill="#16477d"/></svg>
    <p class="web">Visit: <b>www.brightpathwellbeing.net</b></p>
    <p class="call">Call to schedule: <b>833-412-7086</b></p>
  </footer>
</main>
</body>
</html>
```